Schlichtes Design für Malerbetrieb
Zielgruppe
Wir sind ein mittelgroßer Malerbetrieb in München mit umfangreichem Leistungsspektrum.
Unsere Hauptleistungen sind: Fassadenrenovierung, Altbausanierung, Betoninstandsetzung, Balkonabdichtung (kein Neubau!).
Unsere Zielgruppen sind: Hausverwaltungen, Firmen und Privatpersonen.
Unsere Kunden schätzen: Konstruktive Organisation und Planung im Vorfeld, Zuverlässigkeit, saubere Arbeitsweise, dauerhafte Balkonabdichtungen.
Aufgabenstellung
Wir möchten eine langlebige, stilvolle, minimalistische Homepage.
Wir möchten von der bestehenden Homepage nur die Schriftart für unseren Firmennamen (Century Gothic) und wenn möglich (nicht zwingend), irgendwo das florale Muster einbauen. Corporate-Design haben wir nicht.
Farbtöne: Firmennamen Orange (hellorange bis erdiges Orange möglich, da sind wir nicht fixiert) , einen dunklen Hintergrundfarbton (Petrol-Blaugrau ?) mit gelbem (neon bis senfgelb) Akzent (Linien), Blumenmuster weiß, grau.
Dies sind nur unsere Ideen. Wir sind aber auch absolut offen für eure Profi-Ideen.
Wir möchten uns von den unzähligen langweiligen 'Pinselseiten mit veralteten Bilder' unserer Kollegen interessant und mit Stil abheben.
Eher nach dem Motto 'weniger ist mehr'.
Einen positiven, sympathischen Eindruck geben und unsere Leistungen in den Vordergrund bringen.
Da wir viele Stammkunden haben, betreiben wir kein Social-Media und möchten dies vorerst auch nicht tun.
Die Seite wird in den nächsten Jahren nicht verändert, höchstens die Bilder aktualisiert.
Die Texte haben wir alle selbst entworfen und möchten wir so übernehmen.
Die Galerien sollen unkompliziert anzuschauen sein.
Uns gefällt die Struktur und Schlichtheit von https://vaartmolen.nl/ oder Timbra.de gut und wir mögen Vintage-Grafiken gerne.
Einerseits darf die Seite geradlinig, andererseits aber auch rund und floral wirken.

```html
<!DOCTYPE html>
<html lang="de">
<head>
<meta charset="utf-8">
<title>Kolbrit – Leistungen</title>
<link href="https://fonts.googleapis.com/css2?family=Questrial&family=Encode+Sans+Semi+Condensed:wght@300;400&display=swap" rel="stylesheet">
<style>
  :root{
    --orange:#e06a0c;
    --orange-muted:#c86a2c;
    --beige:#ece5df;
    --ink:#2a2624;
    --panel:rgba(236,233,236,0.86);
    --footer:#1f262e;
    --footer-line:#8a6a4a;
    --white:#ffffff;
  }
  *{box-sizing:border-box;margin:0;padding:0}
  html,body{width:1200px;height:1115px;overflow:hidden}
  body{position:relative;font-family:"Questrial",sans-serif;color:var(--ink);background:var(--white)}
  .abs{position:absolute}

  .hero-photo{left:0;top:0;width:753px;height:748px;
    background:linear-gradient(160deg,#f7f1e4 0%,#efe3cc 35%,#e6d4b6 60%,#c9a77a 85%,#b08254 100%)}
  .side-panel{left:753px;top:0;width:447px;height:416px;background:var(--beige)}
  .side-accent{left:753px;top:416px;width:447px;height:332px;background:var(--orange)}

  .brand{left:76px;top:64px;font-size:22px;letter-spacing:.5px;color:var(--orange);font-weight:700}
  .main-nav{top:71px;left:0;width:1200px;height:20px}
  .main-nav a{position:absolute;font-size:15px;color:var(--ink);text-decoration:none;white-space:nowrap}
  .main-nav a.active{color:var(--orange);font-weight:700}

  .service-head{left:76px;top:370px;width:603px;height:46px;background:var(--orange);color:var(--white)}
  .service-head h1{position:absolute;left:35px;top:14px;font-size:14px;font-weight:700}
  .service-head svg{position:absolute;left:626px;top:18px}
  .service-body{left:76px;top:416px;width:603px;height:301px;background:var(--panel);padding:35px 35px 0 35px}
  .service-body p{font-size:12.6px;line-height:15.3px;margin-bottom:15.3px;width:540px}
  .service-body b{font-weight:700}

  .sub-nav{left:753px;top:245px;width:167px;text-align:right}
  .sub-nav a{display:block;font-size:15px;color:var(--ink);text-decoration:none;height:33.7px}
  .sub-nav a.active{color:var(--orange);font-weight:700}

  .facade-photo{left:943px;top:193px;width:181px;height:276px;
    background:linear-gradient(180deg,#d9cfc3 0%,#e6ddd0 40%,#cfc3b1 75%,#8a7258 100%)}

  .about-btn{left:943px;top:646px;width:181px;height:35px;border:1px solid #3a2a20;
    font-size:11.5px;letter-spacing:1.6px;text-align:center;line-height:33px;color:var(--ink);font-weight:700}

  .gallery-intro{left:0;top:748px;width:254px;height:223px;
    background:linear-gradient(180deg,#d07433 0%,#c86a2c 100%)}
  .gallery-intro h2{position:absolute;left:75px;top:143px;font-size:25px;font-weight:400;color:var(--white)}
  .gallery-intro svg{position:absolute;left:182px;top:146px}

  .shot{top:748px;height:223px}
  .shot-book{left:254px;width:306px;background:linear-gradient(180deg,#ece7e0 0%,#d9d2ca 45%,#c24a2a 62%,#1f2634 78%,#151a22 100%)}
  .shot-door{left:560px;width:137px;background:linear-gradient(180deg,#efe6d4 0%,#d9c8a6 40%,#6a3a22 65%,#c8b89a 100%)}
  .shot-square{left:697px;width:231px;background:linear-gradient(180deg,#9fc2d8 0%,#cdb98a 35%,#e5d3a6 65%,#bdb8b0 100%)}
  .shot-hands{left:928px;width:272px;background:linear-gradient(135deg,#d7c9b8 0%,#c99a86 45%,#b96f5e 75%,#c8b4a4 100%)}

  .site-footer{left:0;top:971px;width:1200px;height:144px;background:var(--footer);
    font-family:"Encode Sans Semi Condensed",sans-serif;font-weight:300;color:var(--white);font-size:11.8px}
  .footer-rule{position:absolute;left:76px;top:49px;width:1049px;height:1px;background:var(--footer-line)}
  .copyright{position:absolute;left:76px;top:73px}
  .legal a{position:absolute;top:73px;color:var(--white);text-decoration:none;white-space:nowrap}
  .social-dot{position:absolute;left:1111px;top:73px;width:13px;height:13px;border-radius:50%;background:var(--white)}
</style>
</head>
<body>
  <div class="abs hero-photo" role="img" aria-label="Heller Altbauraum mit Stuckdecke, hohen Fenstern und Parkettboden"></div>
  <div class="abs side-panel"></div>
  <div class="abs side-accent"></div>

  <div class="abs brand">kolbrit</div>
  <nav class="abs main-nav">
    <a style="left:597px" href="#">Home</a>
    <a class="active" style="left:670px" href="#">Leistungen</a>
    <a style="left:776px" href="#">Portrait</a>
    <a style="left:856px" href="#">Referenzen</a>
    <a style="left:964px" href="#">Ausbildung</a>
    <a style="left:1072px" href="#">Kontakt</a>
  </nav>

  <section>
    <header class="abs service-head">
      <h1>Malerarbeiten</h1>
      <svg width="24" height="11" viewBox="0 0 24 11" aria-hidden="true">
        <path d="M6 1 L2 5.5 L6 10 M18 1 L22 5.5 L18 10" fill="none" stroke="#fff" stroke-width="1.6"/>
      </svg>
    </header>
    <div class="abs service-body">
      <p>Flächen, die einheitlich und streifenlos erscheinen, erfreuen den Betrachter. Sie unterstützen primär die optische Erscheinung eines Objekts. Auf längere Zeit gesehen leisten Anstriche jedoch weitere wesentliche Dienste. Sie schützen Ihr Gebäude oder Ihre Wohnung vor Witterungseinflüssen, mechanischer Beschädigung und dem Nagen der Zeit. <b>Unsere Tätigkeit und unser Fachwissen schützen Ihren Besitz.</b></p>
      <p>Bei der Erstellung von baulichen Schutzmaßnahmen müssen alle Objektgegebenheiten mit einbezogen werden. Um einen dauerhaften Bestand von Objekten zu gewährleisten, muss jeder Beteiligte über das eigene Aufgabengebiet hinweg denken.</p>
      <p>Wir betrachten bei der Ausarbeitung unserer Leistungen jedes Bauteil gesondert mit seinen Eigenschaften. Die stets erneuerten Technologien von Anstrichmitteln in Bezug auf Oberflächen-beschaffenheit, Umweltverträglichkeit und Beständigkeit setzen wir jederzeit optimal ein. <b>Nur Fachleute suchen nach Ursachen und erarbeiten die richtigen Lösungen.</b></p>
    </div>
  </section>

  <nav class="abs sub-nav">
    <a class="active" href="#">Malerarbeiten</a>
    <a href="#">Farbgestaltung</a>
    <a href="#">Schimmelsarnierung</a>
    <a href="#">Wärmedämmung</a>
  </nav>

  <div class="abs facade-photo" role="img" aria-label="Altbaufassade mit Balkonen und Rundbogentür"></div>
  <div class="abs about-btn">Über uns</div>

  <section>
    <div class="abs gallery-intro" role="img" aria-label="Galerie-Einstieg mit orange getöntem Altbaufoto">
      <h2>Galerie</h2>
      <svg width="50" height="23" viewBox="0 0 50 23" aria-hidden="true">
        <rect x="0.5" y="0.5" width="21" height="22" fill="none" stroke="#fff"/>
        <rect x="28.5" y="0.5" width="21" height="22" fill="none" stroke="#fff"/>
        <path d="M13 7 L9 11.5 L13 16 M37 7 L41 11.5 L37 16" fill="none" stroke="#fff" stroke-width="1.4"/>
      </svg>
    </div>
    <div class="abs shot shot-book" role="img" aria-label="Fachbuch zu Maler- und Lackierarbeiten"></div>
    <div class="abs shot shot-door" role="img" aria-label="Historische Holztür in verzierter Fassade"></div>
    <div class="abs shot shot-square" role="img" aria-label="Altstadtplatz mit historischem Gebäude"></div>
    <div class="abs shot shot-hands" role="img" aria-label="Hände an bröckelndem Putz"></div>
  </section>

  <footer class="abs site-footer">
    <div class="footer-rule"></div>
    <div class="copyright">© Copyright Kolbrit GmbH 2009 - 2020, Alle Rechte vorbehalten.</div>
    <div class="legal">
      <a style="left:775px" href="#">Impressum</a>
      <a style="left:849px" href="#">Rechtliche Hinweisse</a>
      <a style="left:978px" href="#">Datenschutzerklärung</a>
    </div>
    <span class="social-dot" aria-label="Soziales Netzwerk"></span>
  </footer>
</body>
</html>
```